IT Company requires new Business Card design.

Over the years we have had a few different business card designs. We are now due for new cards across the board for all staff. We felt this would be a good time to start fresh with a new design. Our traditional card simply had our details on the front, and a list of services on the back. We don't particularly need the list of services, we have had cards where the only thing on the rear of the card was our logo.
Feel free to be creative, we would like our tag line "Complete IT Management" to appear at some point, doesn't necessarily have to be with the logo.
I have attached samples and drafts of various previous cards we have used over the years.

```html
<!DOCTYPE html>
<html lang="en">
<head>
<meta charset="utf-8">
<title>Harbor Networks – Business Card</title>
<link href="https://fonts.googleapis.com/css2?family=Source+Sans+3:wght@400;600;700&display=swap" rel="stylesheet">
<style>
  :root {
    --page: #e7e8ec;
    --slate: #5f7482;
    --slate-dark: #4b5d69;
    --paper: #ffffff;
    --ink: #3b3f44;
    --white: #ffffff;
  }
  * { box-sizing: border-box; margin: 0; padding: 0; }
  html, body {
    width: 1200px; height: 987px; overflow: hidden;
    background: var(--page);
    font-family: "Source Sans 3", "Myriad Pro", Arial, sans-serif;
  }
  .sheet {
    width: 1200px; height: 987px;
    display: flex; flex-direction: column; align-items: center; justify-content: center;
    gap: 36px;
  }
  .card {
    position: relative;
    width: 760px; height: 440px;
    border-radius: 26px;
    overflow: hidden;
    box-shadow: 0 6px 18px rgba(0,0,0,0.12);
  }

  /* Front */
  .card-front { background: var(--paper); }
  .brand {
    position: absolute; left: 0; right: 0; top: 44px;
    display: flex; align-items: center; justify-content: center; gap: 18px;
  }
  .brand-square { width: 58px; height: 58px; background: var(--slate); }
  .brand-name {
    color: var(--slate); font-weight: 700; font-size: 58px;
    line-height: 1; letter-spacing: 1px; text-transform: uppercase;
  }
  .rule { position: absolute; left: 0; right: 0; height: 2px; background: var(--slate); }
  .rule-top { top: 150px; }
  .rule-bottom { top: 344px; }
  .band {
    position: absolute; left: 0; right: 0; top: 158px; height: 180px;
    background: var(--slate); color: var(--white);
    display: flex; align-items: center;
  }
  .person { width: 310px; padding-left: 60px; }
  .person-name { font-weight: 700; font-size: 30px; line-height: 1.1; }
  .person-role { font-size: 22px; line-height: 1.3; margin-bottom: 6px; }
  .divider {
    width: 2px; height: 130px;
    background: linear-gradient(to bottom, transparent, rgba(255,255,255,0.8), transparent);
  }
  .contacts { list-style: none; padding-left: 34px; }
  .contact, .person-mobile {
    display: flex; align-items: center; gap: 10px;
    font-size: 22px; line-height: 1.45;
  }
  .icon { width: 18px; height: 18px; flex: none; fill: var(--white); }
  .address {
    position: absolute; left: 0; right: 0; top: 368px;
    text-align: center; color: var(--ink); font-size: 23px;
  }

  /* Back */
  .card-back {
    background: var(--slate); color: var(--white);
    display: flex; flex-direction: column; align-items: center; justify-content: center;
    gap: 28px;
  }
  .back-brand { display: flex; align-items: center; gap: 20px; }
  .back-brand .brand-square { background: var(--white); width: 70px; height: 70px; }
  .back-brand .brand-name { color: var(--white); font-size: 70px; }
  .tagline {
    font-size: 22px; letter-spacing: 6px; text-transform: uppercase;
  }
</style>
</head>
<body>
<main class="sheet">

  <section class="card card-front" aria-label="Card front">
    <div class="brand">
      <span class="brand-square"></span>
      <span class="brand-name">Harbor Networks</span>
    </div>
    <div class="rule rule-top"></div>
    <div class="band">
      <div class="person">
        <p class="person-name">Daniel Reeve</p>
        <p class="person-role">Operation Manager</p>
        <p class="person-mobile">
          <svg class="icon" viewBox="0 0 18 18"><rect x="5" y="1" width="8" height="16" rx="1.5"/><rect x="6.5" y="3" width="5" height="7" fill="#5f7482"/></svg>
          0412 555 018
        </p>
      </div>
      <div class="divider"></div>
      <ul class="contacts">
        <li class="contact">
          <svg class="icon" viewBox="0 0 18 18"><circle cx="9" cy="9" r="8"/><path d="M6 5c1 0 1.5 1.5 1.2 2.2l-.6.6c.5 1.2 1.4 2.1 2.6 2.6l.6-.6c.7-.3 2.2.2 2.2 1.2 0 1-1 1.8-2 1.6C7.4 12.2 5.8 10.6 5.4 8 5.2 7 5 5 6 5z" fill="#5f7482"/></svg>
          08 9555 0140
        </li>
        <li class="contact">
          <svg class="icon" viewBox="0 0 18 18"><rect x="5" y="1" width="8" height="5"/><rect x="1" y="7" width="16" height="7" rx="1.5"/><rect x="5" y="12" width="8" height="5"/></svg>
          08 9555 0141
        </li>
        <li class="contact">
          <svg class="icon" viewBox="0 0 18 18"><rect x="1" y="4" width="16" height="11" rx="1"/><path d="M1.5 4.5 9 10l7.5-5.5" fill="none" stroke="#5f7482" stroke-width="1.5"/></svg>
          daniel@harbornetworks.com.au
        </li>
        <li class="contact">
          <svg class="icon" viewBox="0 0 18 18"><circle cx="9" cy="9" r="8"/><path d="M1 9h16M9 1c-3 3-3 13 0 16M9 1c3 3 3 13 0 16" fill="none" stroke="#5f7482" stroke-width="1.2"/></svg>
          www.harbornetworks.com.au
        </li>
      </ul>
    </div>
    <div class="rule rule-bottom"></div>
    <p class="address">Unit 7 22 Marlow Road, Kelbrook WA 6150</p>
  </section>

  <section class="card card-back" aria-label="Card back">
    <div class="back-brand">
      <span class="brand-square"></span>
      <span class="brand-name">Harbor Networks</span>
    </div>
    <p class="tagline">Complete IT Management</p>
  </section>

</main>
</body>
</html>
```